Custom unique Stationary design for Logistics company

We need a custom, unique , elegant and luxurious full stationary design using our new logo, following these guidelines:
1- Business card: double sided, both sides uses the navy blue as the background main color (same as the code of the navy blue used in our logo).
2- envelope and folder: also use the same navy blue as the main background color.
3- book cover( notepad cover) : same thing with the navy blue
4- letterhead: feel free to use the combination of the colors in our logo.
5- rest of the items are up to your creativity

Target Market(s)

corporates and other businesses

Industry/Entity Type

Logistics and heavy machines contractors

Requirements
Must have
• Letterhead, business card, envelope, notepad cover, paper, file
Nice to have
• navy blue to be main background color for business card, envelope, notepad cover

```html
<!DOCTYPE html>
<html lang="en">
<head>
<meta charset="utf-8">
<title>Harborline Freight Services – Presentation Folder</title>
<link href="https://fonts.googleapis.com/css2?family=Montserrat:wght@700;800&family=Open+Sans:wght@600;700&display=swap" rel="stylesheet">
<style>
  :root {
    --stage: #eef3f8;
    --navy: #165a82;
    --navy-deep: #0f4a6e;
    --navy-light: #1d6c98;
    --orange: #f0693a;
    --edge-grey: #c9d2da;
    --photo-sky: #8fc3ea;
    --photo-steel: #3f7fb4;
    --photo-white: #f4f8fc;
    --tagline: #a9bccb;
    --white: #ffffff;
  }
  * { margin: 0; padding: 0; box-sizing: border-box; }
  html, body { width: 1200px; height: 847px; overflow: hidden; background: var(--stage); }
  .folder-spread {
    position: absolute; left: 30px; top: 30px;
    width: 1140px; height: 787px;
    display: flex;
    box-shadow: 0 10px 30px rgba(15, 74, 110, .25);
  }
  .folder-panel {
    position: relative; width: 570px; height: 787px; overflow: hidden;
    background: linear-gradient(160deg, var(--navy-light), var(--navy) 45%, var(--navy-deep));
    border-top: 6px solid var(--orange);
  }
  .folder-panel--back { border-right: 1px solid rgba(0,0,0,.18); }
  .panel-art { position: absolute; inset: 0; width: 570px; height: 781px; }

  .brand { position: absolute; font-family: "Montserrat", sans-serif; color: var(--white); }
  .brand-mark { font-weight: 800; letter-spacing: 1px; line-height: 1; }
  .brand-name { font-weight: 700; letter-spacing: 2px; text-transform: uppercase; }

  .brand--back { left: 40px; top: 80px; }
  .brand--back .brand-mark { font-size: 48px; }
  .brand--back .brand-name { font-size: 12px; margin-top: 10px; }

  .brand--front { left: 0; right: 0; top: 170px; text-align: center; }
  .brand--front .brand-mark { font-size: 76px; }
  .brand--front .brand-name { font-size: 18px; margin-top: 16px; color: var(--tagline); }

  .contact-list {
    position: absolute; left: 40px; right: 40px; bottom: 60px;
    display: flex; justify-content: space-between; align-items: flex-end;
    list-style: none;
    font-family: "Open Sans", sans-serif; font-weight: 700; font-size: 12px;
    color: var(--white); text-align: center;
  }
  .contact-item { display: flex; flex-direction: column; align-items: center; gap: 10px; }
  .contact-icon { width: 40px; height: 40px; }
  .contact-item span { display: block; line-height: 1.35; }
</style>
</head>
<body>
<main class="folder-spread">

  <section class="folder-panel folder-panel--back">
    <svg class="panel-art" viewBox="0 0 570 781">
      <defs>
        <linearGradient id="backPhoto" x1="0" y1="0" x2="1" y2="1">
          <stop offset="0" stop-color="var(--photo-sky)"/>
          <stop offset=".6" stop-color="var(--photo-steel)"/>
          <stop offset="1" stop-color="var(--navy)"/>
        </linearGradient>
      </defs>
      <path d="M0,0 L570,0 L570,30 C530,250 320,250 180,370 C90,450 25,550 0,640 Z" fill="var(--edge-grey)"/>
      <path d="M0,0 L570,0 L570,20 C520,235 310,235 168,355 C80,435 18,530 0,610 Z"
            fill="url(#backPhoto)" role="img" aria-label="Photo of cargo trucks and shipping containers with a glowing world network overlay"/>
    </svg>
    <div class="brand brand--back">
      <div class="brand-mark">Harborline</div>
      <div class="brand-name">Freight Services</div>
    </div>
    <ul class="contact-list">
      <li class="contact-item">
        <svg class="contact-icon" viewBox="0 0 40 40"><circle cx="20" cy="20" r="20" fill="var(--orange)"/><circle cx="22" cy="17" r="6" fill="none" stroke="var(--white)" stroke-width="2.5"/><line x1="17.5" y1="21.5" x2="12" y2="27" stroke="var(--white)" stroke-width="3" stroke-linecap="round"/></svg>
        <span>000-000-0000<br>harborlinefreight.com</span>
      </li>
      <li class="contact-item">
        <svg class="contact-icon" viewBox="0 0 40 40"><circle cx="20" cy="20" r="20" fill="var(--orange)"/><rect x="10" y="13" width="20" height="14" fill="none" stroke="var(--white)" stroke-width="2"/><polyline points="10,13 20,21 30,13" fill="none" stroke="var(--white)" stroke-width="2"/></svg>
        <span>info@harborlinefreight.com</span>
      </li>
      <li class="contact-item">
        <svg class="contact-icon" viewBox="0 0 40 40"><circle cx="20" cy="20" r="20" fill="var(--orange)"/><polygon points="20,10 30,19 27,19 27,28 13,28 13,19 10,19" fill="var(--white)"/><rect x="18" y="22" width="4" height="6" fill="var(--orange)"/></svg>
        <span>Example Address</span>
      </li>
    </ul>
  </section>

  <section class="folder-panel folder-panel--front">
    <svg class="panel-art" viewBox="0 0 570 781">
      <defs>
        <linearGradient id="frontPhoto" x1="0" y1="0" x2="0" y2="1">
          <stop offset="0" stop-color="var(--photo-white)"/>
          <stop offset=".55" stop-color="var(--photo-sky)"/>
          <stop offset="1" stop-color="var(--photo-white)"/>
        </linearGradient>
      </defs>
      <path d="M0,740 C20,570 180,520 320,480 C450,440 540,380 570,240 L570,745 L0,745 Z" fill="var(--edge-grey)"/>
      <path d="M10,745 C30,585 190,535 328,495 C455,458 545,400 570,262 L570,745 Z"
            fill="url(#frontPhoto)" role="img" aria-label="Illustration of a city skyline, world map, airplane, container ship and delivery trucks"/>
      <rect x="0" y="745" width="570" height="36" fill="var(--navy)"/>
    </svg>
    <div class="brand brand--front">
      <div class="brand-mark">Harborline</div>
      <div class="brand-name">Freight Services</div>
    </div>
  </section>

</main>
</body>
</html>
```